Fixwell and guard Word doc project

Fixwell & Guard are an established home appliance repair and warranty provider looking to rebrand the letters sent to our customers with a new and fresh design.
Please refer to our website for our colour scheme and logo which we are not looking to change:
www.fixwellandguard.co.uk
The letters which we are looking to have redesigned are:
Welcome letters / confirmation paperwork
Basic letter template
Welcome letters:
Page 1 – Opening / Welcome
Page 2 – Plan documentation details
Page 3 & 4 – Terms & Conditions
We can provide a copy of our current welcome / confirmation letters but as we are looking for full redesign, we are looking to steer away from what we have been using historically.
We will be running further projects and we are looking to use the same designer which we pick from this competition so please consider this when submitting your designs.
UPDATE - 01/11/23
An example of our current Welcome documentation has been uploaded for the purpose of example of the placement of the content. As per the brief, we are not looking for a similar design but purely uploading the current documentation to give you an idea of what we are currently using.
Look and feel
Each slider illustrates characteristics of the customer's brand and the style your logo design should communicate.

```html
<!DOCTYPE html>
<html lang="en">
<head>
<meta charset="utf-8">
<title>Fixwell &amp; Guard – Welcome Pack</title>
<link href="https://fonts.googleapis.com/css2?family=Montserrat:wght@400;500;600;700&display=swap" rel="stylesheet">
<style>
:root{
  --blue:#1616d6;
  --blue-light:#3a3ae8;
  --green:#1f9a3e;
  --green-dark:#167a30;
  --ink:#1d1d1d;
  --grey:#444;
}
*{box-sizing:border-box;margin:0;padding:0}
html,body{width:1200px;height:5382px;overflow:hidden;background:#fff}
body{position:relative;font-family:'Montserrat',Arial,sans-serif;color:var(--ink)}
.page{position:absolute;left:180px;width:826px;height:1167px;background:#fff;box-shadow:0 6px 16px rgba(0,0,0,.28);overflow:hidden}
.page-1{top:97px}.page-2{top:1336px}.page-3{top:2571px}.page-4{top:3806px}
.deco{position:absolute;left:0;top:0}
.pattern{position:absolute;left:0;top:0;width:300px;height:150px;background:linear-gradient(135deg,rgba(90,90,255,.55),rgba(22,22,214,0));}
.brand-name{position:absolute;display:flex;align-items:center;justify-content:center;text-align:center;color:var(--blue);font-weight:600;text-transform:uppercase;letter-spacing:.5px}
.sender{position:absolute;left:78px;top:208px;color:#fff;font-weight:600;font-size:14px;line-height:18px}
.recipient{position:absolute;left:78px;top:338px;color:#fff;font-size:17px;line-height:22px}
.salutation{position:absolute;left:78px;top:452px;color:#fff;font-size:17px}
.date{position:absolute;left:612px;top:452px;font-size:17px;font-weight:500}
.letter-body{position:absolute;left:76px;top:580px;width:674px;font-size:16px;line-height:23px;text-align:justify}
.letter-body p+p{margin-top:23px}
.signoff{position:absolute;left:76px;top:942px;font-size:17px;line-height:22px;font-weight:500}
.footer-contact{position:absolute;left:0;top:1076px;width:826px;height:46px;color:#fff;font-size:24px;font-weight:500}
.footer-contact span{position:absolute;top:8px;display:flex;align-items:center;gap:8px}
.footer-contact .phone{left:104px}.footer-contact .web{left:366px}
.page-title{position:absolute;left:78px;top:110px;color:#fff;font-size:24px;font-weight:700}
.page-title em{font-style:normal;color:var(--green)}
.plan{position:absolute;left:78px;width:672px}
.plan-label{position:absolute;left:0;top:0;color:var(--blue);font-weight:700;font-size:16px}
.price{position:absolute;left:114px;top:-4px;width:70px;height:26px;background:var(--green);color:#fff;font-weight:700;font-size:15px;text-align:center;line-height:26px}
.plan-photo{position:absolute;left:0;top:38px;width:183px;height:146px;border-radius:6px}
.plan-details{position:absolute;left:218px;top:0;width:454px}
.plan-details h4{color:var(--blue);font-size:13px;font-weight:700;margin:0 0 10px}
.ticks{list-style:none;font-size:10.8px;line-height:14px;color:var(--grey);margin-bottom:14px}
.ticks li{position:relative;padding-left:20px}
.ticks li::before{content:"";position:absolute;left:2px;top:2px;width:8px;height:8px;border:1.5px solid var(--blue);border-radius:50%}
.ticks.two-col{display:grid;grid-template-columns:160px 1fr}
.terms{position:absolute;left:78px;top:196px;width:672px;height:850px;overflow:hidden;font-size:10.4px;line-height:12.6px;color:var(--grey);text-align:justify}
.terms h3{color:var(--blue);font-size:13px;font-weight:700;margin:18px 0 6px}
.terms h3.green{color:var(--green)}
.terms h3:first-child{margin-top:0}
.terms p{margin-bottom:10px}
.terms ul{list-style:none;margin-top:4px}
.terms ul li{position:relative;padding-left:12px;margin-bottom:15px}
.terms ul li::before{content:"";position:absolute;left:0;top:4px;width:5px;height:5px;background:var(--green);border-radius:50%}
</style>
</head>
<body>

<!-- Page 1: welcome letter -->
<section class="page page-1">
  <svg class="deco" width="826" height="1167" viewBox="0 0 826 1167">
    <polygon points="0,0 826,0 826,40 325,522 0,522" fill="var(--blue)"/>
    <rect x="768" y="522" width="58" height="645" fill="var(--green)"/>
    <polygon points="50,1167 110,1030 826,1030 826,1167" fill="var(--green)"/>
    <polygon points="600,1030 826,1030 826,1167 700,1167" fill="var(--green-dark)" opacity=".5"/>
    <circle cx="589" cy="235" r="158" fill="#fff" stroke="var(--blue)" stroke-width="10"/>
    <polygon points="72,1076 758,1076 746,1122 60,1122" fill="var(--blue)"/>
  </svg>
  <div class="pattern" role="img" aria-label="Faceted hexagon pattern in blue tones"></div>
  <div class="brand-name" style="left:449px;top:215px;width:280px;height:40px;font-size:25px">Fixwell &amp; Guard</div>
  <div class="sender">Fixwell &amp; Guard LTD<br>Alder House<br>First Floor, 14 Marlow Road<br>Hove BN3 4QT</div>
  <div class="recipient">To,<br>Lorem ipsum dolor<br>Designation Here</div>
  <div class="salutation">Dear Sir,</div>
  <div class="date">Date: 21/10/2023</div>
  <div class="letter-body">
    <p>Lorem ipsum dolor sit amet, consectetuer adipiscing elit, sed diam nonummy nibh euismod tincidunt ut laoreet dolore magna aliquam erat volutpat. Ut wisi enim ad minim veniam, quis nostrud exerci tation ullamcorper suscipit lobortis nisl ut aliquip ex ea commodo consequat. Duis autem vel eum iriure dolor in hendrerit in vulputate velit esse molestie consequat, vel illum dolore eu feugiat nulla facilisis at vero eros et accumsan et iusto odio dignissim qui blandit praesent luptatum zzril delenit augue duis dolore te feugait nulla facilisi.</p>
    <p>Lorem ipsum dolor sit amet, cons ectetuer adipiscing elit, sed diam nonummy nibh euismod tincidunt ut laoreet dolore magna aliquam erat volutpat. Ut wisi enim ad minim veniam, quis nostrud exerci tation ullamcorper suscipit lobortis nisl ut aliquip ex ea commodo consequat.</p>
  </div>
  <div class="signoff">Lorem ipsum dolor<br>Company Director</div>
  <div class="footer-contact">
    <span class="phone"><svg width="22" height="22" viewBox="0 0 24 24"><path d="M6.6 10.8a15 15 0 0 0 6.6 6.6l2.2-2.2a1 1 0 0 1 1-.25 11 11 0 0 0 3.6.6 1 1 0 0 1 1 1V20a1 1 0 0 1-1 1A17 17 0 0 1 3 4a1 1 0 0 1 1-1h3.5a1 1 0 0 1 1 1c0 1.25.2 2.45.6 3.6a1 1 0 0 1-.25 1z" fill="#fff"/></svg>0800 321 7788</span>
    <span class="web"><svg width="22" height="22" viewBox="0 0 24 24" fill="none" stroke="#fff" stroke-width="2"><circle cx="12" cy="12" r="9"/><ellipse cx="12" cy="12" rx="4" ry="9"/><line x1="3" y1="12" x2="21" y2="12"/></svg>www.fixwellandguard.co.uk</span>
  </div>
</section>

<!-- Page 2: plan options -->
<section class="page page-2">
  <svg class="deco" width="826" height="1167" viewBox="0 0 826 1167">
    <rect x="0" y="0" width="703" height="160" fill="var(--blue)"/>
    <rect x="768" y="525" width="58" height="642" fill="var(--green)"/>
    <polygon points="50,1167 110,1045 826,1045 826,1167" fill="var(--green)"/>
    <polygon points="600,1045 826,1045 826,1167 700,1167" fill="var(--green-dark)" opacity=".5"/>
    <circle cx="703" cy="103" r="80" fill="#fff" stroke="var(--blue)" stroke-width="9"/>
    <polygon points="72,1076 758,1076 746,1122 60,1122" fill="var(--blue)"/>
  </svg>
  <div class="pattern" role="img" aria-label="Faceted hexagon pattern in blue tones"></div>
  <div class="brand-name" style="left:628px;top:90px;width:150px;height:26px;font-size:13px">Fixwell &amp; Guard</div>
  <h2 class="page-title">Choose the <em>cover you need</em></h2>

  <div class="plan" style="top:206px">
    <div class="plan-label">1 Appliance</div><div class="price">£9.93</div>
    <div class="plan-photo" role="img" aria-label="Bright white kitchen interior" style="background:linear-gradient(135deg,#e9ecef,#b9c0c6 60%,#7e8a72)"></div>
    <div class="plan-details">
      <h4>What's Included:</h4>
      <ul class="ticks"><li>The machine must be under 10 years old.</li><li>No bills for parts and labour.</li><li>Unlimited call out fees.</li><li>24-hour repair line.</li><li>Trusted Expert Engineers.</li><li>You will get a new for old replacement if the appliance cannot be fixed. The machine is based on specification, not price.</li></ul>
      <h4>What's Not Included</h4>
      <ul class="ticks two-col"><li>Accidental Damage.</li><li>Machine not in good working order.</li><li>Cosmetic Damage.</li><li>Indirect Cost.</li><li>Malicious Damage.</li><li>First 30 days.</li></ul>
    </div>
  </div>

  <div class="plan" style="top:480px">
    <div class="plan-label">3 Appliances</div><div class="price" style="left:120px">£19.41</div>
    <div class="plan-photo" role="img" aria-label="Dark kitchen worktop with sink and tap" style="background:linear-gradient(160deg,#2b2f33,#11171b 55%,#9aa0a4)"></div>
    <div class="plan-details">
      <h4>What's Included:</h4>
      <ul class="ticks"><li>The machine must be under 10 years old.</li><li>No bills for parts and labour.</li><li>Unlimited call out fees.</li><li>24-hour repair line.</li><li>Trusted Expert Engineers.</li><li>You will get a new for old replacement if the appliance cannot be fixed. The machine is based on specification, not price.</li></ul>
      <h4>What's Not Included</h4>
      <ul class="ticks two-col"><li>Accidental Damage.</li><li>Machine not in good working order.</li><li>Cosmetic Damage.</li><li>Indirect Cost.</li><li>Malicious Damage.</li><li>First 30 days.</li></ul>
    </div>
  </div>

  <div class="plan" style="top:762px">
    <div class="plan-label">5 Appliances</div><div class="price" style="left:120px">£26.05</div>
    <div class="plan-photo" role="img" aria-label="Kitchen with built-in ovens and fridge" style="background:linear-gradient(135deg,#efe6d8,#c7b9a2 55%,#8d8f93)"></div>
    <div class="plan-details">
      <h4>What's Included:</h4>
      <ul class="ticks"><li>The machine must be under 10 years old.</li><li>No bills for parts and labour.</li><li>Unlimited call out fees.</li><li>24-hour repair line.</li><li>Trusted Expert Engineers.</li><li>You will get a new for old replacement if the appliance cannot be fixed. The machine is based on specification, not price.</li></ul>
      <h4>What's Not Included</h4>
      <ul class="ticks two-col"><li>Accidental Damage.</li><li>Machine not in good working order.</li><li>Cosmetic Damage.</li><li>Indirect Cost.</li><li>Malicious Damage.</li><li>First 30 days.</li></ul>
    </div>
  </div>

  <div class="footer-contact">
    <span class="phone"><svg width="22" height="22" viewBox="0 0 24 24"><path d="M6.6 10.8a15 15 0 0 0 6.6 6.6l2.2-2.2a1 1 0 0 1 1-.25 11 11 0 0 0 3.6.6 1 1 0 0 1 1 1V20a1 1 0 0 1-1 1A17 17 0 0 1 3 4a1 1 0 0 1 1-1h3.5a1 1 0 0 1 1 1c0 1.25.2 2.45.6 3.6a1 1 0 0 1-.25 1z" fill="#fff"/></svg>0800 321 7788</span>
    <span class="web"><svg width="22" height="22" viewBox="0 0 24 24" fill="none" stroke="#fff" stroke-width="2"><circle cx="12" cy="12" r="9"/><ellipse cx="12" cy="12" rx="4" ry="9"/><line x1="3" y1="12" x2="21" y2="12"/></svg>www.fixwellandguard.co.uk</span>
  </div>
</section>

<!-- Page 3: terms part one -->
<section class="page page-3">
  <svg class="deco" width="826" height="1167" viewBox="0 0 826 1167">
    <rect x="0" y="0" width="703" height="160" fill="var(--blue)"/>
    <rect x="768" y="525" width="58" height="642" fill="var(--green)"/>
    <polygon points="50,1167 110,1045 826,1045 826,1167" fill="var(--green)"/>
    <polygon points="600,1045 826,1045 826,1167 700,1167" fill="var(--green-dark)" opacity=".5"/>
    <circle cx="703" cy="103" r="80" fill="#fff" stroke="var(--blue)" stroke-width="9"/>
    <polygon points="72,1076 758,1076 746,1122 60,1122" fill="var(--blue)"/>
  </svg>
  <div class="pattern" role="img" aria-label="Faceted hexagon pattern in blue tones"></div>
  <div class="brand-name" style="left:628px;top:90px;width:150px;height:26px;font-size:13px">Fixwell &amp; Guard</div>
  <h2 class="page-title">Terms and <em>Conditions</em></h2>
  <div class="terms">
    <h3>Terms and conditions of Service</h3>
    <p>This page tells you the terms and conditions on which we supply any of our services listed on our website www.fixwellandguard.co.uk (our website) to you. Please read these terms and conditions carefully and make sure that you understand them before ordering anything from our site. You should understand that by ordering anything from us, you agree to be bound by these terms and conditions.</p>
    <h3>Information About Us</h3>
    <p>We, Fixwell and Guard Limited, operate the website www.fixwellandguard.co.uk. We are registered in England and Wales under company number 12345678 and have our registered office at: Alder House, 14 Marlow Road, Hove BN3 4QT.</p>
    <h3>Plan Terms and Conditions</h3>
    <p>Your policy start date is shown on your plan schedule, for all cases where a plan has started after the expiration of your manufacturers warranty.</p>
    <p>It is important for your benefit and protection that you read these terms and conditions. These and your certificate, and any changes we notify you about (at renewal or otherwise), form your agreement with us. We intend to rely on the terms and conditions set out in this document. Full protection will start thirty (30) days after your application is processed, during the first thirty (30) days you will be provided telephone assistance only, as any faults reported within the initial thirty (30) days will be considered pre-existing. After this initial thirty (30) day period you will be entitled to telephone and full engineering assistance as per your terms and conditions.</p>
    <h3>Definitions</h3>
    <p>Plan: this contract of services.</p>
    <p>Product(s): the appliance(s) protected by this plan, as shown on your certificate.</p>
    <p>We/us/our: Fixwell &amp; Guard Ltd, the provider of the plan. You/your: the person named on your certificate.</p>
    <p>Your certificate: the personalised section of your plan documentation, sent to you once you have taken out a plan or at renewal.</p>
    <h3>Eligibility</h3>
    <p>You must be at least 18 years old and resident in the United Kingdom to be eligible. Your product must be in good working order when this plan starts.</p>
    <h3>Contract of services</h3>
    <p>This plan is not categorised as an insurance product and therefore insurance regulation does not apply. This plan is a contract of services and is governed by UK laws and regulations concerning service contracts.</p>
    <h3>Contract of services</h3>
    <p>Conditions</p>
    <p>The following conditions apply to this plan:</p>
    <ul>
      <li>You must provide us with all relevant information that we request when you apply for the plan. All information you give must not be false, exaggerated or misleading;</li>
      <li>Your product must have been installed, maintained and used in accordance with the manufacturer's instructions;</li>
      <li>Your product must be owned by you and kept only for domestic use.</li>
      <li>Your product must be used in a private home, solely occupied by a single household (at the address you gave to us);</li>
      <li>Your product must be easily accessible and meet all relevant safety</li>
      <li>standards and be safe to work on; and</li>
    </ul>
  </div>
  <div class="footer-contact">
    <span class="phone"><svg width="22" height="22" viewBox="0 0 24 24"><path d="M6.6 10.8a15 15 0 0 0 6.6 6.6l2.2-2.2a1 1 0 0 1 1-.25 11 11 0 0 0 3.6.6 1 1 0 0 1 1 1V20a1 1 0 0 1-1 1A17 17 0 0 1 3 4a1 1 0 0 1 1-1h3.5a1 1 0 0 1 1 1c0 1.25.2 2.45.6 3.6a1 1 0 0 1-.25 1z" fill="#fff"/></svg>0800 321 7788</span>
    <span class="web"><svg width="22" height="22" viewBox="0 0 24 24" fill="none" stroke="#fff" stroke-width="2"><circle cx="12" cy="12" r="9"/><ellipse cx="12" cy="12" rx="4" ry="9"/><line x1="3" y1="12" x2="21" y2="12"/></svg>www.fixwellandguard.co.uk</span>
  </div>
</section>

<!-- Page 4: terms part two -->
<section class="page page-4">
  <svg class="deco" width="826" height="1167" viewBox="0 0 826 1167">
    <rect x="0" y="0" width="703" height="160" fill="var(--blue)"/>
    <rect x="768" y="525" width="58" height="642" fill="var(--green)"/>
    <polygon points="50,1167 110,1045 826,1045 826,1167" fill="var(--green)"/>
    <polygon points="600,1045 826,1045 826,1167 700,1167" fill="var(--green-dark)" opacity=".5"/>
    <circle cx="703" cy="103" r="80" fill="#fff" stroke="var(--blue)" stroke-width="9"/>
    <polygon points="72,1076 758,1076 746,1122 60,1122" fill="var(--blue)"/>
  </svg>
  <div class="pattern" role="img" aria-label="Faceted hexagon pattern in blue tones"></div>
  <div class="brand-name" style="left:628px;top:90px;width:150px;height:26px;font-size:13px">Fixwell &amp; Guard</div>
  <h2 class="page-title">Terms and <em>Conditions</em></h2>
  <div class="terms">
    <h3>Your obligations</h3>
    <p>You must arrange any work required to make your product accessible and compliant with all relevant safety standards and safe to work on, e.g. you will be responsible for carrying out work required to fix a gas leak.</p>
    <h3>What this plan includes</h3>
    <p>Breakdown</p>
    <p>If your product suffers a mechanical or electrical breakdown after the end of the manufacturer's parts and labour guarantee period, our customer services team will try to resolve the problem over the telephone. If we are not able to resolve the problem, we will, at our discretion, decide whether to approve a repair. Where a repair is approved, we will then authorise an engineer to carry out your repair, or we may also (at our option), decide to replace or pay the cost of replacing your product, in each case subject to these terms and conditions.</p>
    <h3>How to request repair</h3>
    <p>To request a repair please contact us as soon as possible by telephone. The telephone number will be shown on your plan document.</p>
    <h3>Limits of the plan</h3>
    <p>There is no limit to the number of repairs you can request unless your plan ends.</p>
    <h3>Repairs information</h3>
    <p>Information we may require</p>
    <p>You must give us all information we need to verify your repair request. You should send any requested documents to the address in 'Customer services details' below.</p>
    <h3 class="green">Important information about repairs</h3>
    <p>Only engineers approved by us are authorised to carry out repairs under this plan, unless we agree otherwise in advance. Repairs will be carried out within the repairer's normal working hours (which are at least 9am to 5pm, Monday to Friday) on a date agreed with you. Please have your plan documentation to hand when the repairer arrives. If your product breaks down, you must take reasonable steps to limit damage, e.g. stop using it if this is likely to cause further damage.</p>
    <h3 class="green">Replacements</h3>
    <p>If a repair is approved, we may (at our option), decide to replace your product with a new product of the same or similar technical specification.</p>
    <h3 class="green">What happens if your product is replaced?</h3>
    <p>If we decide to replace your product any unpaid fee for the current plan period will become due. No fee paid will be refunded. When your product is replaced (or you have received our contribution) your plan will continue on the new appliance with twelve (12) months of cover, or the remainder of your plan period, whichever is shorter.</p>
    <h3 class="green">Product disposal and delivery, installation and other costs</h3>
    <p>If the product is taken or sent away from your home for repair and is then replaced, the original product will become our property and we will dispose of it. If your product remains in your home but is replaced, you will be responsible for disposing of it at your own cost. We do not cover the costs of installation for integrated, built in, or freestanding appliances, nor do we cover the costs for removal of previous appliances.</p>
    <h3 class="green">What happens if we decide not to repair or replace?</h3>
    <p>If we decide not to approve a repair or replacement request which would otherwise fall within the terms of your plan, we will inform you. All fee payments you have made in the current period of your plan will be refunded and your plan will end immediately. No further amounts will be payable. We'll confirm this in writing to the last address you gave us.</p>
  </div>
  <div class="footer-contact">
    <span class="phone"><svg width="22" height="22" viewBox="0 0 24 24"><path d="M6.6 10.8a15 15 0 0 0 6.6 6.6l2.2-2.2a1 1 0 0 1 1-.25 11 11 0 0 0 3.6.6 1 1 0 0 1 1 1V20a1 1 0 0 1-1 1A17 17 0 0 1 3 4a1 1 0 0 1 1-1h3.5a1 1 0 0 1 1 1c0 1.25.2 2.45.6 3.6a1 1 0 0 1-.25 1z" fill="#fff"/></svg>0800 321 7788</span>
    <span class="web"><svg width="22" height="22" viewBox="0 0 24 24" fill="none" stroke="#fff" stroke-width="2"><circle cx="12" cy="12" r="9"/><ellipse cx="12" cy="12" rx="4" ry="9"/><line x1="3" y1="12" x2="21" y2="12"/></svg>www.fixwellandguard.co.uk</span>
  </div>
</section>

</body>
</html>
```